Weightloss company needs Business Card

We want a business card that is clean and professional, yet portrays that we are a friendly, innovative, and versatile program designed to fit the needs of our clients.
I would like there to be 2 sides, one side having an appointment card, and the other side containing the logo and business information. There can be decorations on both sides. The logo is attached.

Target Market(s)

Men and women 40-60

Industry/Entity Type

Business

Contact Information for Business Card

Font styles to use
Sans Serif

Requirements
Must have
• The logo, space for business information
Nice to have
• The colors in the logo
Should not have
• No pictures of people or food

```html
<!DOCTYPE html>
<html lang="en">
<head>
<meta charset="utf-8">
<title>RisePath Wellness – Business Card</title>
<link href="https://fonts.googleapis.com/css2?family=Open+Sans:wght@400;600;700&display=swap" rel="stylesheet">
<style>
  :root {
    --brand-red: #e8213a;
    --brand-blue: #3ab4e6;
    --ink: #1f1f1f;
    --rule: #333333;
    --card: #ffffff;
    --backdrop: #e6e7ea;
  }
  * { margin: 0; padding: 0; box-sizing: border-box; }
  html, body { width: 1200px; height: 900px; overflow: hidden; }
  body {
    background: var(--backdrop);
    font-family: "Open Sans", Arial, sans-serif;
    color: var(--ink);
    position: relative;
  }
  .card {
    position: absolute;
    left: 170px;
    width: 860px;
    height: 420px;
  }
  .card--appointment { top: 20px; }
  .card--contact { top: 460px; }
  .card-shape { position: absolute; inset: 0; width: 860px; height: 420px; }
  .card-shape .body { fill: var(--card); stroke: var(--rule); stroke-width: 1.5; }
  .card-shape .sweep { fill: none; stroke: var(--brand-red); stroke-width: 26; }

  .brand {
    position: absolute;
    display: flex;
    align-items: center;
    gap: 10px;
    color: var(--brand-red);
    font-weight: 700;
    white-space: nowrap;
  }
  .brand-dot { border-radius: 50%; background: var(--brand-red); }
  .card--appointment .brand { left: 490px; top: 150px; font-size: 30px; }
  .card--appointment .brand-dot { width: 14px; height: 14px; }
  .card--contact .brand { left: 440px; top: 175px; font-size: 42px; }
  .card--contact .brand-dot { width: 18px; height: 18px; }

  .appointment-title {
    position: absolute; left: 60px; top: 205px;
    color: var(--brand-red); font-size: 19px; letter-spacing: 0.5px;
  }
  .appointment-field {
    position: absolute; left: 60px; width: 640px;
    display: flex; align-items: flex-end; gap: 10px;
    font-size: 19px;
  }
  .appointment-field .rule { flex: 1; border-bottom: 1.5px solid var(--rule); height: 1px; margin-bottom: 6px; }
  .field-name { top: 245px; }
  .field-date { top: 295px; }
  .field-time { top: 345px; }

  .person { position: absolute; left: 60px; top: 160px; }
  .person-name { color: var(--brand-red); font-size: 34px; font-weight: 400; letter-spacing: 0.5px; }
  .person-role { color: var(--brand-blue); font-size: 18px; font-weight: 600; margin-top: -2px; }
  .address { position: absolute; left: 60px; top: 245px; font-size: 19px; line-height: 1.3; }
  .contact-list { position: absolute; left: 60px; top: 310px; list-style: none; font-size: 19px; line-height: 1.3; }
  .contact-list li { display: flex; align-items: center; gap: 12px; }
  .contact-list svg { width: 16px; height: 16px; fill: none; stroke: var(--brand-blue); stroke-width: 2; }
</style>
</head>
<body>

<section class="card card--appointment" aria-label="Appointment side">
  <svg class="card-shape" viewBox="0 0 860 420">
    <defs>
      <clipPath id="shape-a">
        <path d="M30 110 H470 C540 30 720 20 800 110 C870 190 860 340 780 400 H30 Q0 400 0 370 V140 Q0 110 30 110 Z"/>
      </clipPath>
    </defs>
    <path class="body" d="M30 110 H470 C540 30 720 20 800 110 C870 190 860 340 780 400 H30 Q0 400 0 370 V140 Q0 110 30 110 Z"/>
    <path class="sweep" clip-path="url(#shape-a)" d="M470 110 C540 30 720 20 800 110 C870 190 860 340 780 400"/>
  </svg>
  <div class="brand"><span>RisePath Wellness</span><span class="brand-dot"></span></div>
  <p class="appointment-title">APPOINTMENT</p>
  <div class="appointment-field field-name"><span>Name:</span><span class="rule"></span></div>
  <div class="appointment-field field-date"><span>Date:</span><span class="rule"></span></div>
  <div class="appointment-field field-time"><span>Time:</span><span class="rule"></span></div>
</section>

<section class="card card--contact" aria-label="Contact side">
  <svg class="card-shape" viewBox="0 0 860 420">
    <defs>
      <clipPath id="shape-b">
        <path d="M30 110 H470 C540 30 720 20 800 110 C870 190 860 340 780 400 H30 Q0 400 0 370 V140 Q0 110 30 110 Z"/>
      </clipPath>
    </defs>
    <path class="body" d="M30 110 H470 C540 30 720 20 800 110 C870 190 860 340 780 400 H30 Q0 400 0 370 V140 Q0 110 30 110 Z"/>
    <path class="sweep" clip-path="url(#shape-b)" d="M470 110 C540 30 720 20 800 110 C870 190 860 340 780 400"/>
  </svg>
  <div class="brand"><span>RisePath Wellness</span><span class="brand-dot"></span></div>
  <div class="person">
    <h1 class="person-name">MARCUS HALE</h1>
    <p class="person-role">DIRECTOR</p>
  </div>
  <p class="address">Cedar Road, 21430<br>Lakeside, Coastal Region</p>
  <ul class="contact-list">
    <li><svg viewBox="0 0 16 16"><path d="M3 2 L6 2 L7 5 L5.5 6.5 Q7 9.5 9.5 10.5 L11 9 L14 10 L14 13 Q8 14 3 8 Q2 5 3 2 Z"/></svg>+330 2555-0148</li>
    <li><svg viewBox="0 0 16 16"><rect x="1.5" y="3.5" width="13" height="9"/><path d="M1.5 3.5 L8 9 L14.5 3.5"/></svg>info@risepathwellness.com</li>
    <li><svg viewBox="0 0 16 16"><circle cx="8" cy="8" r="6.5"/><path d="M1.5 8 H14.5 M8 1.5 Q4 8 8 14.5 M8 1.5 Q12 8 8 14.5"/></svg>www.risepathwellness.com</li>
  </ul>
</section>

</body>
</html>
```